Talvoro bonds (Surety bond broker)

We are a broker of surety bonds, we need a presentation and a flyer with fresh design. Our core values are reliable, on time and customized service. We want to transmit to our clients, they can leave on us the process of underwriting and issuing a surety bond, so they can focus on their business with no distractions.

Font styles to use
Sans Serif
Other font styles liked:

Requirements
Must have
• Visually attractive.
Main Message: Fast service issuing and underwriting surety bonds, reliable, nos surprises, we are always one step ahead, customized and personalized bonding solutions.
Nice to have
• Have short version for the flyer, and extended version for the presentation.
Should not have
• We already have a logo (attached), maintain colors

```html
<!DOCTYPE html>
<html lang="es">
<head>
<meta charset="utf-8">
<title>Talvoro Seguros y Fianzas — Tríptico</title>
<link rel="stylesheet" href="https://fonts.googleapis.com/css2?family=Montserrat:wght@300;400;500;600;700;800&display=swap">
<style>
:root{
  --stage:#2f2f2f;
  --green:#6cb33f;
  --green-soft:#a8d08d;
  --grey-dark:#575757;
  --grey-mid:#626262;
  --white:#ffffff;
  --ink:#2b2b2b;
  --text-grey:#4a4a4a;
  --text-light:#e9e9e9;
}
*{margin:0;padding:0;box-sizing:border-box}
html,body{width:853px;height:1200px;overflow:hidden}
body{background:radial-gradient(ellipse at 50% 45%,#3c3c3c,var(--stage));font-family:"Montserrat",sans-serif;position:relative}
.sheet{position:absolute;left:58px;width:737px;height:521px;box-shadow:0 6px 18px rgba(0,0,0,.45)}
.sheet-outer{top:54px}
.sheet-inner{top:627px}
.panel{position:absolute;top:0;width:246px;height:521px;overflow:hidden}
.p1{left:0}.p2{left:246px;width:245px}.p3{left:491px}
.bg-white{background:var(--white)}
.bg-dark{background:var(--grey-dark)}
.bg-mid{background:var(--grey-mid)}
.abs{position:absolute}
.heading{font-weight:500;font-size:16px;line-height:1.1;letter-spacing:.1px}
.heading .hl{color:var(--green)}
.on-dark{color:var(--white)}
.on-light{color:var(--ink)}
.dash{position:absolute;width:12px;height:2px;background:var(--green)}
.dash-white{background:var(--white)}
.dash-black{background:var(--ink)}
.body-text{font-size:7.6px;line-height:10.9px;font-weight:400}
.body-text p{margin-bottom:7.5px}
.justify{text-align:justify}
.hl{color:var(--green)}
.photo{position:absolute;border-radius:50%}
.ring{position:absolute;border-radius:50%;border:1px solid var(--green)}
.partners{position:absolute;left:20px;top:52px;width:200px;height:200px;border-radius:50%;background:var(--white)}
.partner{position:absolute;font-size:7.4px;font-weight:600;color:#4b4b4b;display:flex;align-items:center;gap:3px;white-space:nowrap}
.partner i{display:inline-block;width:8px;height:8px;border-radius:50%;background:#9a9a9a}
.brand{position:absolute;display:flex;flex-direction:column;align-items:flex-end}
.brand-name{font-weight:400;color:var(--green);letter-spacing:1px;display:flex;align-items:center;gap:5px}
.brand-name b{display:inline-block;border-radius:50%;background:var(--green)}
.brand-tag{color:var(--white);font-weight:700;letter-spacing:2px}
.contact-name{font-size:8.8px;font-weight:600;color:var(--green);margin-top:5px}
.contact-line{font-size:9px;font-weight:500;color:var(--white);display:flex;align-items:center;gap:8px;height:13px;margin-left:-16px}
.ci{width:8px;height:8px;border-radius:50%;border:1px solid #8fbf6f;flex:none}
.services li{list-style:none;font-size:8.2px;font-weight:600;color:var(--white);line-height:10.5px;padding-left:10px;position:relative;margin-bottom:7.5px}
.services li::before{content:"✓";position:absolute;left:0;top:0;color:var(--green);font-weight:400}
.services small{display:block;font-size:5.2px;font-weight:400;color:#ddd;line-height:9px}
.product{position:absolute;left:23px;width:80px;height:80px;border-radius:50%;background:var(--green);border:2px solid var(--white);box-shadow:0 0 0 2px var(--green);display:flex;align-items:center;justify-content:center;color:var(--white);font-size:8px;font-weight:500}
.plist{position:absolute;left:116px;font-size:8px;line-height:11.8px;color:#e6e6e6;list-style:none}
.plist .tick{color:var(--green)}
.plist .tick::before{content:"✓ ";color:var(--white)}
.plist .dot::before{content:"● ";font-size:6px;color:var(--white);vertical-align:1px}
.special h3{font-size:10.4px;font-weight:500;color:var(--green);line-height:12.5px;margin-bottom:6px}
.special .body-text{color:var(--text-grey)}
.informes{position:absolute;left:30px;top:443px;width:195px;height:30px;background:var(--green);color:var(--white);font-weight:700;font-size:20px;letter-spacing:1px;display:flex;align-items:center;justify-content:center}
.mail{position:absolute;left:22px;top:480px;width:205px;text-align:center;font-weight:700;font-size:14.5px;color:#111}
</style>
</head>
<body>

<!-- Outer face -->
<section class="sheet sheet-outer">
  <!-- About -->
  <div class="panel p1 bg-white">
    <h2 class="heading on-light abs" style="left:29px;top:27px">¿Quiénes <span class="hl" style="font-weight:700">somos?</span></h2>
    <span class="dash" style="left:29px;top:52px"></span>
    <div class="body-text abs" style="left:29px;top:66px;width:190px;color:var(--text-grey)">
      <p>Talvoro Bonds, somos un grupo de jóvenes emprendedores, con amplia experiencia en el sector afianzador.</p>
      <p>Estamos convencidos de que nuestro principal diferenciador es la pasión por el servicio.</p>
      <p>Nuestra prioridad es el éxito de cada uno de nuestros clientes, nos aseguramos de que el “trámite” de fianzas deje de ser un “trámite” y se convierta en la llave del éxito para cada uno de nuestros fiados y beneficiarios.</p>
      <p>Buscamos siempre tener relaciones estrechas y de largo plazo con todos nuestros ”stakeholders”. Por lo que nos rodeamos del mejor talento en el sector para garantizar a nuestros clientes un servicio personalizado, en tiempo y confiable.</p>
    </div>
    <div class="ring" style="left:-13px;top:289px;width:246px;height:246px"></div>
    <div class="photo" role="img" aria-label="Fotografía de una obra en construcción con grúa y trabajadores" style="left:2px;top:296px;width:226px;height:226px;background:linear-gradient(170deg,#6aa6d8 0%,#a9cbe6 40%,#c9a46a 72%,#6b4a2c 100%)"></div>
    <div class="abs" style="left:128px;top:275px;width:68px;height:68px;border-radius:50%;background:var(--green-soft);opacity:.85"></div>
    <div class="abs" style="left:184px;top:329px;width:40px;height:40px;border-radius:50%;background:var(--green-soft);opacity:.85"></div>
  </div>

  <!-- Partners & contact -->
  <div class="panel p2 bg-mid">
    <h2 class="abs" style="left:0;width:245px;top:28px;text-align:center;color:var(--green);font-size:11.6px;font-weight:700">Nuestro Socios de Negocio</h2>
    <div class="ring" style="left:15px;top:53px;width:210px;height:210px"></div>
    <div class="partners" style="left:20px;top:58px">
      <span class="partner" style="left:60px;top:26px"><i></i>Afianzadora Norvel</span>
      <span class="partner" style="left:26px;top:55px"><i></i>Corvista</span>
      <span class="partner" style="left:112px;top:55px"><i></i>Halden Marine</span>
      <span class="partner" style="left:26px;top:83px">Brenmor</span>
      <span class="partner" style="left:106px;top:83px"><i></i>Fianzas Soldane</span>
      <span class="partner" style="left:26px;top:111px"><i></i>Varesta Fianzas</span>
      <span class="partner" style="left:112px;top:111px"><i></i>Cautemex</span>
      <span class="partner" style="left:34px;top:141px">Delmora</span>
      <span class="partner" style="left:110px;top:141px">Fianzas Orbe</span>
    </div>
    <div class="brand" style="left:28px;top:280px;width:120px">
      <span class="brand-name" style="font-size:21px"><b style="width:9px;height:9px"></b>TALVORO</span>
      <span class="brand-tag" style="font-size:4.6px">SEGUROS Y FIANZAS</span>
    </div>
    <h2 class="heading on-dark abs" style="left:41px;top:319px;font-size:14px">Contacto</h2>
    <span class="dash" style="left:41px;top:340px"></span>
    <div class="abs" style="left:43px;top:349px">
      <div class="contact-name">Lucía Medrano</div>
      <div class="contact-line"><span class="ci"></span>lmedrano@talvoro.com</div>
      <div class="contact-line"><span class="ci"></span>55 0142 7381</div>
      <div class="contact-name">Marta Ibarra</div>
      <div class="contact-line"><span class="ci"></span>mibarra@talvoro.com</div>
      <div class="contact-line"><span class="ci"></span>55 0163 5529</div>
      <div class="contact-name">Rodrigo Salvat</div>
      <div class="contact-line"><span class="ci"></span>rsalvat@talvoro.com</div>
      <div class="contact-line"><span class="ci"></span>55 0187 2064</div>
      <div class="contact-line" style="margin-top:11px"><span class="ci"></span>www.talvoro.com</div>
    </div>
  </div>

  <!-- Cover -->
  <div class="panel p3 bg-dark" style="overflow:visible">
    <div class="brand" style="left:28px;top:33px;width:186px">
      <span class="brand-name" style="font-size:32px"><b style="width:13px;height:13px"></b>TALVORO</span>
      <span class="brand-tag" style="font-size:6.8px;margin-top:1px">SEGUROS Y FIANZAS</span>
    </div>
  </div>
  <div class="ring" style="left:432px;top:94px;width:292px;height:292px"></div>
  <div class="photo" role="img" aria-label="Fotografía de dos ingenieros con casco y chaleco revisando planos frente a una grúa" style="left:438px;top:100px;width:280px;height:280px;background:linear-gradient(160deg,#4e8fd1 0%,#9cc6ea 45%,#d7d36a 70%,#5c6b7a 100%)"></div>
  <div class="abs" style="left:528px;top:404px">
    <div style="font-size:23px;font-weight:700;color:var(--white);line-height:25px">Tu éxito..</div>
    <div style="font-size:23px;font-weight:800;color:var(--green);line-height:25px">nuestra pasión</div>
  </div>
  <span class="dash" style="left:529px;top:469px;width:20px;height:3px"></span>
  <div class="abs" style="left:529px;top:488px;display:flex;align-items:center;gap:6px;font-size:10px;letter-spacing:3.6px;color:var(--white);font-weight:500"><span class="ci"></span>www.talvoro.com</div>
</section>

<!-- Inner face -->
<section class="sheet sheet-inner">
  <!-- Value & services -->
  <div class="panel p1 bg-dark">
    <h2 class="heading on-dark abs" style="left:28px;top:27px">Nuestra oferta <span class="hl">de valor</span></h2>
    <span class="dash dash-white" style="left:29px;top:54px"></span>
    <div class="body-text justify abs" style="left:29px;top:68px;width:196px;color:var(--text-light)">
      <p><span class="hl">Para nuestros fiados,</span> nos aseguramos de que el proceso de emisión de fianzas sea <span class="hl">claro, rápido y sencillo.</span> Dando una asesoría personalizada y seguimiento puntual a cada solicitud.</p>
      <p>Sabemos la importancia de tener una fianza en tiempo y sin errores, por lo que nos empeñamos en siempre ir un paso adelante, permitiendo que nuestros clientes se despreocupen del proceso de afianzamiento y logren todos sus objetivos.</p>
      <p><span class="hl">Para nuestros beneficiarios,</span> trabajamos solo con las mejores afianzadoras del país y garantizamos que todos nuestros clientes cuenten con una garantía confiable, que les permita concluir sus proyectos con la tranquilidad de que tienen un respaldo confiable. Nuestro compromiso es siempre mitigar los riesgos y nunca dejar desprotegidos a nuestros clientes</p>
    </div>
    <h2 class="heading on-dark abs" style="left:28px;top:284px">Nuestros <span class="hl">Servicios</span></h2>
    <span class="dash dash-white" style="left:29px;top:309px"></span>
    <ul class="services abs" style="left:29px;top:322px;width:200px">
      <li>Asesoría personalizada para la obtención de Líneas de Afianzamiento</li>
      <li>Emisión y administración de fianzas.<small>(Fidelidad, Administrativas, Judiciales, Crédito y Fideicomisos)</small></li>
      <li>Diseño, implementación y gestión de esquemas de afianzamiento.</li>
      <li>Asesoría en riesgos para contratos de obra, suministro y proveeduría.</li>
      <li>Colocación de fianzas internacionales y reaseguro.</li>
      <li>Asesoría legal en proceso de reclamación de fianzas.</li>
      <li>Esquemas de afianzamiento masivos.</li>
    </ul>
  </div>

  <!-- Bond products -->
  <div class="panel p2 bg-mid">
    <h2 class="heading on-dark abs" style="left:33px;top:27px">Productos en <span class="hl">Fianzas</span></h2>
    <span class="dash dash-white" style="left:34px;top:54px"></span>
    <svg class="abs" style="left:0;top:0" width="245" height="521" viewBox="0 0 245 521" aria-hidden="true">
      <g stroke="#ffffff" stroke-width=".8" fill="none">
        <path d="M103 121 H168"/>
        <path d="M66 257 V270 H168"/>
        <path d="M66 368 V391 H168"/>
        <path d="M66 489 V501 H168"/>
      </g>
      <g fill="#6cb33f"><circle cx="168" cy="121" r="1.8"/><circle cx="168" cy="270" r="1.8"/><circle cx="168" cy="391" r="1.8"/><circle cx="168" cy="501" r="1.8"/></g>
    </svg>
    <div class="product" style="top:74px">Fidelidad</div>
    <div class="product" style="top:178px">Judicial</div>
    <div class="product" style="top:289px">Administrativas</div>
    <div class="product" style="top:409px">Crédito</div>
    <ul class="plist" style="top:91px"><li class="tick">Colectiva</li><li class="tick">Individual</li></ul>
    <ul class="plist" style="top:149px">
      <li class="tick">Penales</li><li class="dot">Libertad provisional</li><li class="dot">Condena provisional</li><li class="dot">Reparación del daño</li><li class="dot">Sanción pecuniaria</li>
      <li class="tick">No Penales</li><li class="dot">Daños y prejuicios</li><li class="dot">Pensión alimenticia</li><li class="dot">Laboral</li>
    </ul>
    <ul class="plist" style="top:288px">
      <li class="tick">Obra y Proveeduría</li><li class="dot">Cumplimiento</li><li class="dot">Anticipo</li><li class="dot">Buena Calidad</li><li class="dot">Contingencias Laborales</li>
      <li class="tick" style="margin-top:3px">Arrendamiento</li><li class="tick">Contingencias ambientales</li><li class="tick">Fiscales</li>
    </ul>
    <ul class="plist" style="top:412px">
      <li class="tick">Compra venta</li><li class="tick">Suministro</li><li class="dot">Red Eléctrica</li><li class="dot">Estaciones de Servicio</li><li class="dot">Petrolera Sur</li><li class="dot">Aeropuertos</li><li class="tick">Otras Crédito</li>
    </ul>
  </div>

  <!-- Special products -->
  <div class="panel p3 bg-white">
    <h2 class="heading on-light abs" style="left:29px;top:27px">Productos <span class="hl">Especiales</span></h2>
    <span class="dash dash-black" style="left:30px;top:55px"></span>
    <div class="special abs" style="left:29px;top:73px;width:188px">
      <h3>Flujo Garantizado</h3>
      <div class="body-text justify"><p>Es una fianza con la que se constituye un fondo colectivo para productos masivos que permite darle viabilidad financiera a tu empresa, proporcionándole el flujo constante de recursos para cubrir posibles pérdidas por quebrantos de créditos o cuentas por cobrar no liquidadas por sus clientes.</p></div>
    </div>
    <div class="special abs" style="left:29px;top:190px;width:188px">
      <h3>Esquemas de Proveedores</h3>
      <div class="body-text justify">
        <p>Esquema diseñado para grandes beneficiarios, que permite proteger los recursos invertidos en proyectos de construcción y adquisición de bienes o prestación de servicios, garantizando las obligaciones que se derivan de estos a cargo de sus proveedores o contratistas.</p>
        <p>Este programa permite la fácil administración de fianzas, previniendo un procedimiento ágil para la ejecución y cobro de las garantías que se emitan dentro del esquema.</p>
      </div>
    </div>
    <div class="special abs" style="left:29px;top:352px;width:188px">
      <h3>Programa de<br>garantías de fianzas para PyMEs</h3>
      <div class="body-text"><p>Con este programa puedes incrementar la línea de afianzamiento, gracias a que Fondo Impulsa aporta 50% de las garantías requeridas en fianzas hasta por 30 millones de pesos</p></div>
    </div>
    <div class="informes">INFORMES</div>
    <div class="mail">contacto@talvoro.com</div>
  </div>
</section>

</body>
</html>
```